Mobile version of Desktop site

I need a mobile version of my desktop site. Up until now we have been using a mobile translation service but there are too many drawbacks and bugs. So I need a mobile site designed to be used on an iPhone or android phone that is "Inspired by" our desktop site. I am going to setup two completely separate sites, served either as desktop or mobile.

I have attached an eps version of my logo.

Design this site as though the largest screen it will be viewed on is an iPhone 6 plus, but more likely it will be viewed on smaller screens.

Phone number as a button to click to call should be prominent.

Just need a basic attorney website that is clean and has the look and feel of the desktop site, but readable and usable on a smartphone.

Base your design off of an inner page like whats on this url:
Desktop url: https://www.brackenfieldlaw.com/mesa-verdan.html

Reason: I am extending the deadline to allow for implementation of feedback

Target Market(s)

everyone

Industry/Entity Type

Attorney

Number of Pages Required

1 page

Font styles to use
Sans Serif

Requirements
Must have
• Must be readable and usable on a smart phone, from a 5.5" iPhone 6 plus on down to the original iPhone. I'm looking for usability and readability.
Nice to have
• I would like to see logos shown at the top filling the width of the page if viewed in portrait mode with the phone number next, and it should be a complementing version of my desktop site.
Should not have
• I do not want to see a lot of small details that would be lost on a smartphone platform.

```html
<!DOCTYPE html>
<html lang="en">
<head>
<meta charset="utf-8">
<title>Brackenfield Attorneys — Mobile</title>
<link rel="stylesheet" href="https://fonts.googleapis.com/css2?family=Montserrat:wght@400;500&display=swap">
<style>
  :root{
    --navy:#0b3468;
    --navy-deep:#082a55;
    --navy-glow:#1a5a93;
    --ink:#0f3a6b;
    --grey-text:#7a7a7a;
    --call-text:#555555;
    --bar-top:#e2e2e2;
    --bar-bottom:#f4f4f4;
    --white:#ffffff;
    --field-line:rgba(120,160,210,.45);
    --field-text:#dfe7f2;
  }
  *{box-sizing:border-box;margin:0;padding:0}
  html,body{width:768px;height:1200px;overflow:hidden}
  body{font-family:"Montserrat",sans-serif;background:var(--white);position:relative}

  .call-bar{
    height:84px;display:flex;align-items:center;justify-content:center;
    background:linear-gradient(var(--bar-top),var(--bar-bottom));
    font-size:22px;color:var(--call-text);letter-spacing:.2px;
  }
  .call-bar a{color:var(--ink);font-weight:500;text-decoration:none;margin-left:8px}

  .brand{
    height:160px;display:flex;flex-direction:column;align-items:center;justify-content:center;
    background:var(--white);color:var(--ink);font-weight:500;
  }
  .brand-name{font-size:56px;letter-spacing:1px;line-height:1}
  .brand-sub{font-size:20px;letter-spacing:9px;margin-top:10px}

  .main-nav{
    height:86px;background:var(--navy);display:flex;align-items:center;justify-content:space-between;
    padding:0 38px;color:var(--white);font-size:26px;
  }
  .menu-icon{width:40px;height:34px}

  .hero{
    position:relative;height:280px;
    background:linear-gradient(180deg,#4d5a73 0%,#b98679 38%,#e7a07a 55%,#3b2f34 72%,#6f6a72 100%);
  }
  .hero-arrow{
    position:absolute;top:50%;width:38px;height:38px;margin-top:-19px;border-radius:50%;
    background:#111;display:flex;align-items:center;justify-content:center;
  }
  .hero-arrow.prev{left:26px}
  .hero-arrow.next{right:26px}
  .hero-caption{position:absolute;right:28px;bottom:18px;color:var(--white);font-size:24px}

  .help-intro{height:160px;text-align:center;padding-top:42px;background:var(--white)}
  .help-title{font-size:46px;font-weight:400;color:var(--ink);letter-spacing:.5px}
  .help-sub{font-size:24px;color:var(--grey-text);margin-top:18px}

  .contact-form{
    position:relative;height:430px;
    background:radial-gradient(ellipse 60% 40% at 50% 0%,var(--navy-glow) 0%,var(--navy) 55%,var(--navy-deep) 100%);
    padding-top:80px;
  }
  .form-notch{position:absolute;top:0;left:50%;margin-left:-50px;width:100px;height:22px}
  .field{
    margin:0 auto 14px;width:626px;height:72px;border:1.5px solid var(--field-line);border-radius:3px;
    display:flex;align-items:center;padding-left:32px;color:var(--field-text);font-size:22px;
  }
  .field + .field{margin-top:0}
  .field.phone{margin-top:26px}
</style>
</head>
<body>
  <header>
    <div class="call-bar">CALL FOR FREE CONSULATION <a href="tel:5550142270">(555)014-2270</a></div>
    <div class="brand">
      <div class="brand-name">BRACKENFIELD</div>
      <div class="brand-sub">ATTORNEYS</div>
    </div>
    <nav class="main-nav">
      <span>HOME</span>
      <svg class="menu-icon" viewBox="0 0 40 34" aria-hidden="true">
        <rect x="0" y="1" width="40" height="6" rx="2" fill="#fff"/>
        <rect x="0" y="14" width="40" height="6" rx="2" fill="#fff"/>
        <rect x="0" y="27" width="40" height="6" rx="2" fill="#fff"/>
      </svg>
    </nav>
  </header>

  <section class="hero" role="img" aria-label="Photo of a pier at sunset over the beach">
    <span class="hero-arrow prev"><svg width="14" height="14" viewBox="0 0 14 14"><path d="M9 2 4 7l5 5" stroke="#fff" stroke-width="2" fill="none"/></svg></span>
    <span class="hero-arrow next"><svg width="14" height="14" viewBox="0 0 14 14"><path d="M5 2l5 5-5 5" stroke="#fff" stroke-width="2" fill="none"/></svg></span>
    <span class="hero-caption">Verdan Shore Pier</span>
  </section>

  <section class="help-intro">
    <h1 class="help-title">HOW CAN WE HELP YOU ?</h1>
    <p class="help-sub">TALK TO US ABOUT YOUR INJURY NOW</p>
  </section>

  <section class="contact-form">
    <svg class="form-notch" viewBox="0 0 100 22" aria-hidden="true"><path d="M0 0h100L50 22z" fill="#fff"/></svg>
    <div class="field">NAME</div>
    <div class="field">E-MAIL</div>
    <div class="field phone">PHONE</div>
    <div class="field">DESCRIPTION</div>
  </section>
</body>
</html>
```